Building company buisness cards

We are looking for a sharp modern new look for our business cards.
We are a New Zealand based company that specialises in house and land packages.
We have attached a photo of the current logo and would like to see if it can be improved somehow if needed.
We are open to any colours but we have chosen green at this stage.
Feel free to change the font and make the logo smarter looking.
Play with the colours and see what looks best.

We want a card that looks so good know one will want to throw it away!

Target Market(s)

Home buyers

Industry/Entity Type

Building

Contact Information for Business Card

Derek Tolvane
0217394062
dtolvane@quillmarkhomesteads.co.nz
quillmarkhomesteads.co.nz

Font styles to use
Serif
Sans Serif

Colors

Designer to choose colors to be used in the design.

Requirements
Must have
• Logo and company name on one side, details on the other side
Nice to have
• Color codes for the original green are HEX #4a8028, RGB(74,128,40), CMYK(42,0,69,50)
• Round corners, Raised and/or spot UV

```html
<!DOCTYPE html>
<html lang="en">
<head>
<meta charset="utf-8">
<title>Quillmark Homesteads – Business Card</title>
<link href="https://fonts.googleapis.com/css2?family=Roboto:wght@400&family=Open+Sans:wght@400&display=swap" rel="stylesheet">
<style>
  :root {
    --backdrop: #e4e2de;
    --card-edge: #d9d9d9;
    --brand-green: #2ea836;
    --ink: #1c1c1c;
    --rule-soft: #cfcfcf;
    --icon-fg: #ffffff;
  }
  html, body {
    margin: 0;
    padding: 0;
    width: 1200px;
    height: 1023px;
    overflow: hidden;
    background: var(--backdrop);
  }
  .canvas {
    position: relative;
    width: 1200px;
    height: 1023px;
    display: flex;
    align-items: center;
    justify-content: center;
  }
  .card {
    position: relative;
    width: 900px;
    height: 515px;
    background: linear-gradient(160deg, #ffffff 0%, #f6f6f6 100%);
    border-radius: 34px;
    box-shadow: 0 0 0 1px var(--card-edge), 0 10px 30px rgba(0,0,0,0.12);
  }
  .brand {
    position: absolute;
    top: 110px;
    left: 0;
    width: 100%;
    display: flex;
    flex-direction: column;
    align-items: center;
  }
  .brand-lockup {
    display: flex;
    align-items: center;
    gap: 18px;
  }
  .brand-mark {
    width: 42px;
    height: 42px;
    background: var(--brand-green);
    flex: none;
  }
  .brand-name {
    margin: 0;
    font-family: "Roboto", sans-serif;
    font-weight: 400;
    font-size: 46px;
    line-height: 1;
    color: var(--brand-green);
  }
  .brand-rule {
    width: 70px;
    height: 1px;
    margin-top: 22px;
    background: var(--rule-soft);
  }
  .holder {
    position: absolute;
    left: 120px;
    top: 382px;
    margin: 0;
    font-family: "Roboto", sans-serif;
    font-weight: 400;
    font-size: 34px;
    color: var(--ink);
  }
  .divider {
    position: absolute;
    left: 430px;
    top: 318px;
    width: 2px;
    height: 160px;
    background: var(--ink);
  }
  .contact-list {
    position: absolute;
    left: 470px;
    top: 326px;
    margin: 0;
    padding: 0;
    list-style: none;
    font-family: "Open Sans", sans-serif;
    font-size: 21px;
    color: var(--ink);
  }
  .contact-item {
    display: flex;
    align-items: center;
    gap: 12px;
    height: 36px;
  }
  .contact-icon {
    width: 20px;
    height: 20px;
    flex: none;
  }
</style>
</head>
<body>
<main class="canvas">
  <section class="card" aria-label="Business card front">
    <div class="brand">
      <div class="brand-lockup">
        <span class="brand-mark" aria-hidden="true"></span>
        <h1 class="brand-name">quillmark homesteads</h1>
      </div>
      <div class="brand-rule"></div>
    </div>

    <p class="holder">Derek Tolvane</p>
    <div class="divider"></div>

    <ul class="contact-list">
      <li class="contact-item">
        <svg class="contact-icon" viewBox="0 0 20 20" aria-hidden="true">
          <rect width="20" height="20" fill="var(--brand-green)"/>
          <path d="M6 4 L8.5 4 L9.5 7 L8 8.2 Q9.5 11 11.8 12 L13 10.5 L16 11.5 L16 14 Q15 16 12.5 15.5 Q6.5 13.5 4.5 7.5 Q4 5 6 4 Z" fill="var(--icon-fg)"/>
        </svg>
        <span>0217394062</span>
      </li>
      <li class="contact-item">
        <svg class="contact-icon" viewBox="0 0 20 20" aria-hidden="true">
          <rect width="20" height="20" fill="var(--brand-green)"/>
          <rect x="4" y="6" width="12" height="8.5" fill="none" stroke="var(--icon-fg)" stroke-width="1.5"/>
          <path d="M4 6 L10 11 L16 6" fill="none" stroke="var(--icon-fg)" stroke-width="1.5"/>
        </svg>
        <span>dtolvane@quillmarkhomesteads.co.nz</span>
      </li>
      <li class="contact-item">
        <svg class="contact-icon" viewBox="0 0 20 20" aria-hidden="true">
          <rect width="20" height="20" fill="var(--brand-green)"/>
          <circle cx="10" cy="10" r="5.8" fill="none" stroke="var(--icon-fg)" stroke-width="1.4"/>
          <ellipse cx="10" cy="10" rx="2.4" ry="5.8" fill="none" stroke="var(--icon-fg)" stroke-width="1.2"/>
          <line x1="4.2" y1="10" x2="15.8" y2="10" stroke="var(--icon-fg)" stroke-width="1.2"/>
        </svg>
        <span>quillmarkhomesteads.co.nz</span>
      </li>
    </ul>
  </section>
</main>
</body>
</html>
```